Specialised investor in e-mobility and energy wants business card design

We need a business card design that fits our existing corporate design. <The look and feel must be 'sharp'/'clean', dynamic, communicate momentum, professionalism etc (as one would imagine from a firm in the financial sector). We like the idea of a reverse-side of the card that includes the logo, and the name and contact details on the other. We expect the deliverable to be whatever format might be required to be able to get cards printed directly by a service such as kelmo press. Our website is www.zub.capital

```html
<!DOCTYPE html>
<html lang="en">
<head>
<meta charset="utf-8">
<title>ZUB Capital – Business Card</title>
<link href="https://fonts.googleapis.com/css2?family=Montserrat:wght@400;500;700&display=swap" rel="stylesheet">
<style>
  :root {
    --green-dark: #334f24;
    --green-light: #86b34a;
    --ink: #2b2b2b;
    --paper: #ffffff;
    --backdrop: #dcdcda;
  }
  * { margin: 0; padding: 0; box-sizing: border-box; }
  html, body {
    width: 1200px; height: 801px; overflow: hidden;
    background: var(--backdrop);
    font-family: "Montserrat", sans-serif;
  }
  .sheet {
    position: relative; width: 1200px; height: 801px;
    display: flex; align-items: center; justify-content: center; gap: 40px;
  }
  .card {
    position: relative; width: 540px; height: 308px;
    background: var(--paper);
    border-bottom: 3px solid var(--green-light);
    box-shadow: 0 10px 24px rgba(0,0,0,.18);
    overflow: hidden;
  }
  .card__sweep { position: absolute; inset: 0; width: 100%; height: 100%; }
  .brand {
    position: absolute; display: flex; align-items: center; gap: 8px;
    color: var(--green-dark); font-weight: 500; white-space: nowrap;
  }
  .brand__dot { display: block; border-radius: 50%; background: var(--green-dark); }
  .card--front .brand { left: 92px; top: 168px; font-size: 30px; }
  .card--front .brand__dot { width: 12px; height: 12px; }
  .divider {
    position: absolute; left: 300px; top: 118px; width: 1px; height: 160px;
    background: var(--green-light);
  }
  .details { position: absolute; left: 318px; top: 118px; color: var(--ink); }
  .details__name {
    color: var(--green-light); font-weight: 700; font-size: 17px; letter-spacing: .5px;
  }
  .details__role { font-size: 13px; margin-top: 2px; }
  .contact { list-style: none; margin-top: 14px; font-size: 12.5px; line-height: 19px; }
  .contact li { display: flex; align-items: center; gap: 7px; }
  .contact svg { width: 11px; height: 11px; fill: var(--green-light); flex: none; }
  .details__company { color: var(--green-light); font-size: 13px; margin-top: 12px; }
  .details__city { font-size: 13px; }
  .card--back { display: flex; align-items: center; justify-content: center; }
  .card--back .brand { position: static; font-size: 62px; gap: 16px; }
  .card--back .brand__dot { width: 22px; height: 22px; }
</style>
</head>
<body>
<main class="sheet">
  <section class="card card--front" aria-label="Card front with contact details">
    <svg class="card__sweep" viewBox="0 0 540 308" preserveAspectRatio="none" aria-hidden="true">
      <path d="M0 0 H530 C330 40 110 40 0 102 Z" fill="var(--green-dark)"/>
      <path d="M540 14 V22 C330 58 110 70 0 134 V122 C110 58 330 48 540 14 Z" fill="var(--green-light)"/>
    </svg>
    <div class="brand"><span class="brand__dot"></span>ZUB Capital</div>
    <div class="divider"></div>
    <div class="details">
      <p class="details__name">MARTEN HOLLOWAY</p>
      <p class="details__role">Managing Director</p>
      <ul class="contact">
        <li><svg viewBox="0 0 24 24"><path d="M6.6 10.8a15 15 0 0 0 6.6 6.6l2.2-2.2a1 1 0 0 1 1-.25 11.4 11.4 0 0 0 3.6.57 1 1 0 0 1 1 1V20a1 1 0 0 1-1 1A17 17 0 0 1 3 4a1 1 0 0 1 1-1h3.5a1 1 0 0 1 1 1c0 1.25.2 2.45.57 3.57a1 1 0 0 1-.25 1z"/></svg>+41 70555 0148</li>
        <li><svg viewBox="0 0 24 24"><path d="M2 5h20v14H2z M2 5l10 8 10-8" /></svg>marten@zub.capital</li>
        <li><svg viewBox="0 0 24 24"><circle cx="12" cy="12" r="10"/></svg>www.zub.capital</li>
      </ul>
      <p class="details__company">ZUB Capital S.A.</p>
      <p class="details__city">Geneva, Switzerland</p>
    </div>
  </section>

  <section class="card card--back" aria-label="Card back with company name">
    <div class="brand"><span class="brand__dot"></span>ZUB Capital</div>
  </section>
</main>
</body>
</html>
```